Business card

We need a business card design for our company based in Auckland , New Zealand called 'Ridge + Studio Ltd'. We provide architectural services. We would like to see designs that use the max. three colours (such as white, black, grey) The final design should communicate financial safety and growth."
Also I will provide our company logo. I would like to the logo to be embeded onto our business card.

Target Market(s)

new residential house, alteration & addition & light commericila design & drafting service

Industry/Entity Type

Architecture

Contact Information for Business Card

Company name: ridge + studio Ltd.
Name: Mark Delford
Job title: architectural designer & Design LBP
email address: mark@rplusd.co.nz
mobile number: 02 5163 2290
web site: www.rplusd.co.nz

Requirements
Must have
• My project must have..
• - embeded logo (attached company logo)
• I don't have a bigger version for our company logo, but I have one old one, so you can remove the word from it)
• - insert the attached small BKTW logo & LBP logo
• - creative, simple and clear business card.
• - Max. three colours
Nice to have
• - Here are the samples I would like to share with you: http://www.plimvora.com/blog/minimalistic-business-card-designs/
• I would like to have my business card like one of the creation.
Should not have
• TBA

```html
<!DOCTYPE html>
<html lang="en">
<head>
<meta charset="utf-8">
<title>Ridge + Studio Ltd — Business Card</title>
<link href="https://fonts.googleapis.com/css2?family=PT+Sans+Narrow:wght@400;700&display=swap" rel="stylesheet">
<style>
  :root {
    --backdrop: #2e2f31;
    --card-black: #0c0c0c;
    --card-black-sheen: #262626;
    --card-white: #f4f4f4;
    --card-white-shade: #d9d9d9;
    --ink-white: #ffffff;
    --ink-grey: #bdbdbd;
    --ink-black: #111111;
  }
  * { box-sizing: border-box; margin: 0; padding: 0; }
  html, body {
    width: 1200px;
    height: 950px;
    overflow: hidden;
    background: var(--backdrop);
    font-family: "PT Sans Narrow", "Arial Narrow", sans-serif;
  }
  .canvas {
    position: relative;
    width: 1200px;
    height: 950px;
  }
  .card {
    position: absolute;
    box-shadow: 0 18px 40px rgba(0,0,0,0.45);
  }

  /* Front: black portrait card */
  .card-front {
    left: 140px;
    top: 178px;
    width: 340px;
    height: 595px;
    background: linear-gradient(160deg, var(--card-black) 0%, var(--card-black-sheen) 45%, var(--card-black) 100%);
    color: var(--ink-white);
    text-align: center;
  }
  .contact-block {
    position: absolute;
    top: 70px;
    left: 0;
    width: 100%;
  }
  .person-name {
    font-weight: 700;
    font-size: 30px;
    letter-spacing: 1px;
    text-transform: uppercase;
    line-height: 1.1;
  }
  .person-title {
    font-size: 22px;
    line-height: 1.15;
    margin-top: 4px;
  }
  .divider {
    width: 46px;
    height: 2px;
    background: var(--ink-grey);
    margin: 16px auto 14px;
  }
  .company-name {
    font-weight: 700;
    font-size: 21px;
    margin-bottom: 6px;
  }
  .contact-line {
    font-size: 20px;
    line-height: 1.25;
    color: var(--ink-white);
  }
  .accreditations {
    position: absolute;
    bottom: 44px;
    left: 0;
    width: 100%;
    display: flex;
    justify-content: center;
    align-items: center;
    gap: 62px;
  }
  .badge-association,
  .badge-practitioner {
    display: block;
  }

  /* Back: white landscape card */
  .card-back {
    left: 522px;
    top: 305px;
    width: 595px;
    height: 340px;
    background: linear-gradient(135deg, var(--card-white) 0%, #ffffff 40%, var(--card-white-shade) 100%);
    display: flex;
    align-items: center;
    justify-content: center;
  }
  .brand-lockup {
    display: flex;
    align-items: center;
    gap: 16px;
  }
  .brand-name {
    font-size: 38px;
    font-weight: 700;
    color: var(--ink-black);
    letter-spacing: 0.5px;
  }
</style>
</head>
<body>
<main class="canvas">

  <section class="card card-front" aria-label="Business card front">
    <div class="contact-block">
      <h1 class="person-name">Mark Delford</h1>
      <p class="person-title">architectural designer &amp;<br>Design LBP</p>
      <div class="divider"></div>
      <p class="company-name">ridge + studio Ltd.</p>
      <p class="contact-line">02 5163 2290</p>
      <p class="contact-line">mark@rplusd.co.nz</p>
      <p class="contact-line">www.rplusd.co.nz</p>
    </div>

    <div class="accreditations">
      <svg class="badge-association" width="46" height="46" viewBox="0 0 46 46" role="img" aria-label="Association membership badge">
        <rect x="0" y="0" width="46" height="46" fill="var(--ink-grey)"/>
      </svg>
      <svg class="badge-practitioner" width="62" height="62" viewBox="0 0 62 62" role="img" aria-label="Licensed practitioner badge">
        <circle cx="31" cy="31" r="30" fill="var(--ink-white)"/>
      </svg>
    </div>
  </section>

  <section class="card card-back" aria-label="Business card back">
    <div class="brand-lockup">
      <svg width="40" height="40" viewBox="0 0 40 40" aria-hidden="true">
        <circle cx="20" cy="20" r="17" fill="none" stroke="var(--ink-black)" stroke-width="4"/>
      </svg>
      <span class="brand-name">Ridge + Studio</span>
    </div>
  </section>

</main>
</body>
</html>
```